Tolvik Commercial Cleaning is lookong for a new business card design.

A fresh new design that's professional and stylish. We need a serious upgrade to our business cards. I have included pictures of our existing ones. Our clients include professional individuals and business owners. We woupdblike something professional and upbeat. Please have fun and see what you come uo with.

Target Market(s)

Property managers, business owners, facility managers and other similar professionals

Industry/Entity Type

Janitorial

Contact Information for Business Card

Name, cell, office number, email, web address

Font styles to use
Sans Serif

Colors

Designer to choose colors to be used in the design.

Requirements
Must have
• please use the green color in our logo
Nice to have
• Bar code
Should not have
• Address

```html
<!DOCTYPE html>
<html lang="en">
<head>
<meta charset="utf-8">
<title>Tolvik Commercial Cleaning – Business Card</title>
<link rel="stylesheet" href="https://fonts.googleapis.com/css2?family=Nunito:wght@800&family=Arimo:wght@400&display=swap">
<style>
  :root {
    --brand-green: #2fb14f;
    --brand-blue: #2c5a9e;
    --ink-grey: #555a5e;
    --paper: #f8f8f6;
    --card-dark: #2a2a2a;
    --emboss: #3a3a3a;
    --backdrop: #161616;
  }
  * { box-sizing: border-box; margin: 0; padding: 0; }
  html, body {
    width: 1200px; height: 963px; overflow: hidden;
    background: var(--backdrop);
  }
  .sheet {
    width: 1200px; height: 963px;
    display: flex; flex-direction: column;
    align-items: center; justify-content: center; gap: 56px;
  }
  .card {
    width: 560px; height: 320px;
    border-radius: 22px;
    position: relative; overflow: hidden;
    border-bottom: 4px solid var(--brand-green);
    border-right: 3px solid var(--brand-green);
  }
  /* front */
  .card-front { background: var(--paper); }
  .brand-name {
    position: absolute; top: 62px; left: 250px; width: 270px;
    font-family: "Nunito", sans-serif; font-weight: 800;
    font-size: 34px; line-height: 1.05;
    color: var(--brand-green);
    text-transform: lowercase;
  }
  .holder-name {
    position: absolute; top: 212px; left: 36px;
    font-family: "Nunito", sans-serif; font-weight: 800;
    font-size: 25px; color: var(--brand-green);
    text-transform: lowercase;
  }
  .divider {
    position: absolute; top: 200px; left: 228px;
    width: 1.5px; height: 78px; background: var(--brand-green);
  }
  .contact-list {
    position: absolute; top: 204px; left: 246px;
    list-style: none;
    font-family: "Arimo", sans-serif; font-size: 16px;
    color: var(--ink-grey); line-height: 24px;
  }
  .contact-list li { display: flex; align-items: center; gap: 8px; }
  .contact-list svg { width: 14px; height: 14px; flex: none; }
  /* back */
  .card-back {
    background: var(--card-dark);
    display: flex; align-items: center; justify-content: center;
  }
  .back-name {
    font-family: "Nunito", sans-serif; font-weight: 800;
    font-size: 46px; line-height: 1.05; text-align: center;
    color: var(--emboss); text-transform: lowercase;
  }
</style>
</head>
<body>
<main class="sheet">
  <section class="card card-front" aria-label="Card front">
    <p class="brand-name">Tolvik Commercial Cleaning</p>
    <p class="holder-name">maren castell</p>
    <span class="divider"></span>
    <ul class="contact-list">
      <li>
        <svg viewBox="0 0 16 16" aria-hidden="true"><path d="M3 1.5l3 .5 1 3.5-2 1.3a9 9 0 0 0 4.2 4.2l1.3-2 3.5 1 .5 3C13 14.5 11 15 9 14 5 12 2 8.5 1.5 5 1 3.5 2 2 3 1.5z" fill="var(--brand-green)"/></svg>
        (555) 014-2870
      </li>
      <li>
        <svg viewBox="0 0 16 16" aria-hidden="true"><rect x="1.5" y="3.5" width="13" height="9" rx="1" fill="none" stroke="var(--brand-green)" stroke-width="1.4"/><path d="M2 4l6 5 6-5" fill="none" stroke="var(--brand-green)" stroke-width="1.4"/></svg>
        maren@tolvikcleaning.com
      </li>
      <li>
        <svg viewBox="0 0 16 16" aria-hidden="true"><circle cx="8" cy="8" r="6.5" fill="none" stroke="var(--brand-green)" stroke-width="1.3"/><ellipse cx="8" cy="8" rx="3" ry="6.5" fill="none" stroke="var(--brand-green)" stroke-width="1.1"/><path d="M1.5 8h13M2.5 5h11M2.5 11h11" stroke="var(--brand-green)" stroke-width="1"/></svg>
        www.tolvikcleaning.com
      </li>
    </ul>
  </section>

  <section class="card card-back" aria-label="Card back">
    <p class="back-name">Tolvik Commercial<br>Cleaning</p>
  </section>
</main>
</body>
</html>
```